New letter head for Air Conditioning business

We need a new professional letter head design to suit our new re-branded air conditioning business. Our new logo is attached

```html
<!DOCTYPE html>
<html lang="en">
<head>
<meta charset="utf-8">
<title>Coldfront Letterhead</title>
<link rel="stylesheet" href="https://fonts.googleapis.com/css2?family=Lato:wght@300;400;700&family=Pinyon+Script&display=swap">
<style>
:root{
  --backdrop:#e4e4e4;
  --paper:#f2f2f2;
  --ink:#2f2f2f;
  --body:#4a4a4a;
  --brand-green:#5bb67e;
  --faint:#e3e3e3;
}
*{margin:0;padding:0;box-sizing:border-box}
html,body{width:1200px;height:1200px;overflow:hidden;background:var(--backdrop)}
.letterhead{
  position:absolute;left:175px;top:0;width:849px;height:1200px;
  background:var(--paper);overflow:hidden;
  font-family:"Lato",sans-serif;color:var(--body);
}
.brand-circle-decor{
  position:absolute;right:-150px;bottom:-150px;width:460px;height:460px;
  border-radius:50%;background:var(--faint);
}
.brand{
  position:absolute;top:44px;left:0;width:100%;text-align:center;
}
.brand-name{
  font-family:"Lato",sans-serif;font-weight:700;font-size:40px;letter-spacing:3px;
  color:var(--ink);line-height:1;
}
.brand-mark{
  display:inline-block;width:26px;height:26px;border-radius:50%;
  background:var(--brand-green);vertical-align:middle;margin-right:12px;margin-top:-6px;
}
.brand-tagline{
  font-family:"Lato",sans-serif;font-weight:700;font-size:8.5px;letter-spacing:1.6px;
  color:var(--brand-green);text-transform:uppercase;margin-top:6px;padding-left:38px;
}
.letter{
  position:absolute;left:90px;top:283px;width:668px;
  font-weight:300;font-size:13.3px;line-height:20px;
}
.letter-date{margin-bottom:20px}
.recipient{margin-bottom:40px}
.recipient-name{font-weight:700;color:#111}
.salutation{margin-bottom:20px}
.letter-body p{text-align:justify;margin-bottom:20px}
.closing{margin-top:52px}
.signature{
  font-family:"Pinyon Script",cursive;font-size:30px;color:#222;
  margin:6px 0 0 8px;line-height:1.2;
}
.footer-accent{
  position:absolute;left:0;top:1067px;width:11px;height:105px;background:var(--brand-green);
}
.contact{
  position:absolute;left:56px;top:1065px;font-size:13.3px;line-height:17px;color:#3a3a3a;
  font-weight:400;
}
.contact-address{margin-bottom:5px}
.contact-line{display:flex;align-items:center;gap:7px}
.contact-line svg{width:11px;height:11px;flex:none}
</style>
</head>
<body>
<main class="letterhead">
  <div class="brand-circle-decor"></div>

  <header class="brand">
    <div class="brand-name"><span class="brand-mark"></span>COLDFRONT</div>
    <div class="brand-tagline">Air Conditioning &amp; Refrigeration</div>
  </header>

  <section class="letter">
    <p class="letter-date">01 January 2050</p>
    <address class="recipient" style="font-style:normal">
      <div class="recipient-name">Company (Pvt) Ltd.</div>
      <div>PO Box 3355 Mainville St</div>
      <div>Sample City Country 3355</div>
    </address>
    <p class="salutation">Dear Daniel Hartley,</p>
    <div class="letter-body">
      <p>Lorem ipsum dolor sit amet, consectetuer adipiscing elit, sed diam nonummy nibh euismod tincidunt ut laoreet dolore magna aliquam erat volutpat. Ut wisi enim ad minim veniam, quis nostrud exerci tation ullamcorper suscipit lobortis nisl ut aliquip ex ea commodo consequat. Duis dolore te feugait nulla facilisi. Nam liber tempor cum soluta nobis eleifend option congue nihil imperdiet doming id quod mazim placerat facer possim assum. Lorem ipsum dolor sit amet, consectetuer adipiscing elit, sed diam nonummy nibh euismod tincidunt ut laoreet dolore magna aliquam erat volutpat. Ut wisi enim ad minim veniam, quis nostrud exerci tation ullamcorper suscipit lobortis nisl ut aliquip ex ea commodo consequat.</p>
      <p>Consectetuer adipiscing elit, sed diam nonummy nibh euismod tincidunt ut laoreet dolore magna aliquam erat volutpat. Ut wisi enim ad minim veniam, quis nostrud exerci tation ullamcorper suscipit lobortis nisl ut aliquip ex ea commodo consequat. Consectetuer adipiscing elit, sed diam nonummy nibh euismod tincidunt ut laoreet dolore magna aliquam erat volutpat. Ut wisi enim ad minim veniam, quis nostrud exerci tation ullamcorper suscipit lobortis nisl ut aliquip ex ea commodo consequat.</p>
      <p>Consectetuer adipiscing elit, sed diam nonummy nibh euismod tincidunt ut laoreet dolore magna aliquam erat volutpat. Ut wisi enim ad minim veniam, quis nostrud exerci tation ullamcorper suscipit lobortis nisl ut aliquip ex ea commodo consequat. Consectetuer adipiscing elit, sed diam nonummy nibh euismod tincidunt ut laoreet dolore magna aliquam erat volutpat. Ut wisi enim ad minim veniam, quis nostrud exerci tation ullamcorper suscipit lobortis nisl ut aliquip ex ea commodo consequat.</p>
    </div>
    <p class="closing">Sincerely Yours</p>
    <p class="signature">Marcus Ellery Dane</p>
  </section>

  <div class="footer-accent"></div>
  <footer class="contact">
    <div class="contact-address">Unit 14, Suite<br>Block D, Harlow Rd<br>VIC, Australia 3100</div>
    <div class="contact-line">
      <svg viewBox="0 0 12 12"><path d="M2.5 1.2 4.4 3.4 3.5 4.6c.6 1.5 1.7 2.6 3.2 3.3l1.1-1 2.2 1.9-1 1.5C5.3 10 1.9 6.6 1 2.3z" fill="#5bb67e"/></svg>
      <span>(+1) 200.555.0147</span>
    </div>
    <div class="contact-line">
      <svg viewBox="0 0 12 12"><rect x="0.5" y="2.5" width="11" height="7" fill="#5bb67e"/><path d="M0.8 2.8 6 6.8l5.2-4" fill="none" stroke="#f2f2f2" stroke-width="1"/></svg>
      <span>info@coldfrontair.com</span>
    </div>
    <div class="contact-line">
      <svg viewBox="0 0 12 12"><circle cx="6" cy="6" r="5" fill="none" stroke="#5bb67e" stroke-width="1.1"/><ellipse cx="6" cy="6" rx="2.2" ry="5" fill="none" stroke="#5bb67e" stroke-width="1"/><path d="M1 6h10" stroke="#5bb67e" stroke-width="1"/></svg>
      <span>www.coldfrontair.com</span>
    </div>
  </footer>
</main>
</body>
</html>
```